Business Cards + Flyer + Letterhead for Care Recruitment Agency

We are a recruitment agency for the health & care sector. We need designs made for business cards, A5 double-sided flyer, and a letterhead template.

Our branding message is professionalism, care, compassion, expertise. We are experts in recruitment for the care & health industry.

Our logo source files and colours are here - https://www.filevault-example.net/sh/q8rn27lpzw4xkc/BBRtLm3QPW92dKfYhNvZceLmo?dl=0

For the business card, I have attached an example we like. We want a vertical business card design, something very similar to the example given. The design should match our logo in terms of brand colors. On one side should be our logo, our website (www.holbrookelune.co.uk) and Care Recruitment Specialists written somewhere visible that fits, between our logo and the website at the bottom. On the other side should be our details.

Details on the front:

Logo with slogan
Care Recruitment Specialists
www.holbrookelune.co.uk

Details on the back:

Dominic Argyros
Managing Director

Radley Court, 40-48 Pellow St, Birmingham, B7 9QX
07612 495137
dominic@holbrookelune.co.uk
www.holbrookelune.co.uk

Nadia Holbrooke
Business Development Director

07731 284956
nadia@holbrookelune.co.uk
www.holbrookelune.co.uk

For the A5 flyer, I have attached some pictures we've used for the website, which could be used for the flyer as well. To get a better idea of our branding, please visit our website - https://holbrookelune.co.uk/

The text for the flyer is also attached.

Finally, the letterhead template should be a docx template with our logo and our identifiable branding (the same shapes and matching colours you will come up with for the business cards and flyer).

```html
<!DOCTYPE html>
<html lang="en">
<head>
<meta charset="utf-8">
<title>Holbrooke Lune – Stationery</title>
<link rel="stylesheet" href="https://fonts.googleapis.com/css2?family=Montserrat:wght@600&family=Open+Sans:wght@400;600&family=Raleway:wght@800&family=Arimo:wght@400&display=swap">
<style>
  :root {
    --navy: #0b2f7a;
    --navy-deep: #0d2a66;
    --royal: #0a3c9a;
    --brand-blue: #1a6fff;
    --cyan: #1ea8ff;
    --ink: #222;
    --body-text: #555;
    --rule: #c9c9c9;
    --stage: #e6e7ea;
    --paper: #ffffff;
  }
  * { box-sizing: border-box; margin: 0; padding: 0; }
  html, body {
    width: 1200px; height: 1000px; overflow: hidden;
    background: var(--stage);
  }
  .canvas { position: relative; width: 1200px; height: 1000px; }

  /* ---------- Letterhead ---------- */
  .letterhead {
    position: absolute; left: 30px; top: 40px;
    width: 640px; height: 920px;
    background: var(--paper);
    box-shadow: 0 2px 8px rgba(0,0,0,.12);
    font-family: "Open Sans", Arial, sans-serif;
    color: var(--body-text);
  }
  .letterhead__band {
    position: absolute; left: 0; top: 0; bottom: 0; width: 17px;
    background: linear-gradient(180deg, var(--royal), var(--navy-deep));
  }
  .letterhead__header {
    position: absolute; top: 22px; left: 17px; right: 0;
    display: flex; flex-direction: column; align-items: center;
  }
  .brand-lockup { display: flex; align-items: center; gap: 8px; }
  .brand-lockup__dot {
    width: 34px; height: 34px; border-radius: 50%;
    background: linear-gradient(135deg, var(--cyan), var(--brand-blue));
  }
  .brand-lockup__name {
    font-family: "Montserrat", Arial, sans-serif; font-weight: 600;
    color: var(--navy); font-size: 20px; letter-spacing: 2px;
  }
  .letterhead__strap {
    margin-top: 12px; font-weight: 600; font-size: 11.5px;
    color: var(--ink); letter-spacing: .3px;
  }
  .letterhead__body {
    position: absolute; top: 168px; left: 78px; right: 62px;
    font-size: 10.2px; line-height: 1.5;
  }
  .letterhead__body p { margin-bottom: 12px; }
  .letterhead__body .para { line-height: 18.5px; text-align: justify; margin-bottom: 18px; }
  .letterhead__meta { margin-bottom: 32px !important; }
  .signoff { margin-top: 24px; }
  .signature-mark {
    display: block; width: 148px; height: 20px; margin: 12px 0 8px;
    border-radius: 3px; background: #ececec;
  }
  .signoff__name { font-size: 12px; color: #333; }
  .signoff__role { font-size: 10px; margin-top: 2px; }
  .letterhead__footer {
    position: absolute; left: 17px; right: 0; bottom: 20px;
    text-align: center; font-size: 11.5px; color: #333;
  }
  .letterhead__footer .rule {
    width: 440px; height: 1px; background: var(--rule); margin: 3px auto 4px;
  }
  .letterhead__footer b { color: var(--royal); font-weight: 600; }
  .letterhead__footer .web { color: var(--royal); }

  /* ---------- Business cards ---------- */
  .card {
    position: absolute; top: 560px; width: 220px; height: 356px;
    box-shadow: 0 2px 8px rgba(0,0,0,.18);
  }
  .card--front {
    left: 700px;
    background: linear-gradient(180deg, var(--royal) 0%, var(--navy-deep) 100%);
    color: #fff; text-align: center;
  }
  .card--front .card__mark {
    width: 132px; height: 132px; border-radius: 50%;
    margin: 70px auto 0;
    background: linear-gradient(135deg, var(--cyan), var(--brand-blue));
  }
  .card--front .card__name {
    position: absolute; left: 0; right: 0; top: 280px;
    font-family: "Montserrat", Arial, sans-serif; font-weight: 600;
    font-size: 17px; letter-spacing: 1.6px;
  }
  .card--front .card__strap {
    position: absolute; left: 0; right: 0; top: 318px;
    font-family: "Arimo", Arial, sans-serif; font-size: 8.6px;
    color: var(--cyan); letter-spacing: .2px;
  }

  .card--back {
    left: 950px; background: var(--paper); text-align: center;
    font-family: "Arimo", Arial, sans-serif; color: #111;
  }
  .card--back .brand-lockup {
    position: absolute; top: 64px; left: 0; right: 0; justify-content: center; gap: 6px;
  }
  .card--back .brand-lockup__dot { width: 22px; height: 22px; }
  .card--back .brand-lockup__name { font-size: 13px; letter-spacing: 1.2px; }
  .card__person { position: absolute; top: 192px; left: 0; right: 0; }
  .card__person-name {
    font-family: "Raleway", Arial, sans-serif; font-weight: 800;
    font-size: 15.5px; color: var(--navy-deep);
  }
  .card__person-role { font-size: 10.5px; margin-top: 1px; }
  .icon-row {
    position: absolute; top: 232px; left: 0; right: 0;
    display: flex; justify-content: center; align-items: center; gap: 3px;
  }
  .icon-row .line { width: 30px; height: 1px; background: #888; margin: 0 4px; }
  .icon-box {
    width: 15px; height: 15px; background: var(--navy-deep); border-radius: 2px;
    display: flex; align-items: center; justify-content: center;
  }
  .card__contacts {
    position: absolute; top: 256px; left: 0; right: 0;
    font-size: 10.8px; line-height: 13.5px;
  }
  .card__contacts .web { color: var(--royal); }
  .card__divider { position: absolute; top: 300px; left: 54px; right: 54px; height: 1px; background: #888; }
  .card__address {
    position: absolute; top: 306px; left: 0; right: 0;
    font-size: 10.2px; line-height: 13.5px; color: #222;
  }
</style>
</head>
<body>
<div class="canvas">

  <section class="letterhead">
    <div class="letterhead__band"></div>
    <header class="letterhead__header">
      <div class="brand-lockup">
        <span class="brand-lockup__dot"></span>
        <span class="brand-lockup__name">HOLBROOKE LUNE</span>
      </div>
      <div class="letterhead__strap">CARE RECRUITMENT SPECIALISTS</div>
    </header>

    <div class="letterhead__body">
      <p>Issuing Date: May 5, 2018</p>
      <p class="letterhead__meta">Name Of Employee Mr. XYZABC<br>Address of Employee<br>Address Line 2 etc..</p>
      <p>Dear Mr.XYZABC</p>
      <p class="para">Lorem Ipsum has been the industry's standard dummy text ever since the 1500s, when an unknown printer took a galley of type and scrambled it to make a type specimen book. It has survived not only five centuries, but also the leap into electronic typesetting, remaining essentially unchanged. It was popularised in the 1960s with the release of Letraset sheets containing Lorem Ipsum passages, and more recently with desktop publishing software like Aldus PageMaker including versions of Lorem Ipsum.</p>
      <p class="para">Lorem Ipsum is simply dummy text of the printing and typesetting industry. Lorem Ipsum has been the industry's standard dummy text ever since the 1500s, when an unknown printer took a galley of type and scrambled it to make a type specimen book.</p>
      <p class="para">It has survived not only five centuries, but also the leap into electronic typesetting, remaining essentially unchanged. It was popularised in the 1960s with the release of Letraset sheets containing Lorem IpsumIpsum passages.</p>
      <div class="signoff">
        <p style="margin:0">Yours Sincerely</p>
        <span class="signature-mark" role="img" aria-label="Handwritten signature of Marcus Ellery"></span>
        <div class="signoff__name">Marcus Ellery</div>
        <div class="signoff__role">Managing Director</div>
      </div>
    </div>

    <footer class="letterhead__footer">
      <div>Radley Court, 40-48 Pellow St Birmingham, B7 9QX</div>
      <div class="rule"></div>
      <div><b>P:</b> 07612 495137 | <b>E:</b> dominic@holbrookelune.co.uk | www.<span class="web">holbrookelune</span>.co.uk</div>
    </footer>
  </section>

  <section class="card card--front">
    <div class="card__mark"></div>
    <div class="card__name">HOLBROOKE LUNE</div>
    <div class="card__strap">CARE RECRUITMENT SPECIALISTS</div>
  </section>

  <section class="card card--back">
    <div class="brand-lockup">
      <span class="brand-lockup__dot"></span>
      <span class="brand-lockup__name">HOLBROOKE LUNE</span>
    </div>
    <div class="card__person">
      <div class="card__person-name">DOMINIC ARGYROS</div>
      <div class="card__person-role">Managing Director</div>
    </div>
    <div class="icon-row">
      <span class="line"></span>
      <span class="icon-box"><svg width="10" height="10" viewBox="0 0 10 10"><path d="M1 3.5c0-1 1.5-1.8 4-1.8s4 .8 4 1.8v.8H7V3.3C6.3 3 3.7 3 3 3.3v1H1z" fill="#fff"/><rect x="2" y="4.8" width="6" height="3.8" rx=".6" fill="#fff"/></svg></span>
      <span class="icon-box"><svg width="10" height="10" viewBox="0 0 10 10"><rect x="1" y="2.3" width="8" height="5.6" fill="none" stroke="#fff" stroke-width="1"/><path d="M1 2.5l4 3 4-3" fill="none" stroke="#fff" stroke-width="1"/></svg></span>
      <span class="icon-box"><svg width="10" height="10" viewBox="0 0 10 10"><circle cx="5" cy="5" r="3.8" fill="none" stroke="#fff" stroke-width="1"/><path d="M1.2 5h7.6M5 1.2c-1.8 2-1.8 5.6 0 7.6M5 1.2c1.8 2 1.8 5.6 0 7.6" fill="none" stroke="#fff" stroke-width=".7"/></svg></span>
      <span class="line"></span>
    </div>
    <div class="card__contacts">
      <div>07612 495137</div>
      <div>dominic@holbrookelune.co.uk</div>
      <div>www.<span class="web">holbrookelune</span>.co.uk</div>
    </div>
    <div class="card__divider"></div>
    <div class="card__address">Radley Court, 40-48 Pellow St<br>Birmingham, B7 9QX</div>
  </section>

</div>
</body>
</html>
```